Fin-Tech Firm Captivating Business Card Design

We need a logo design as well to compliment this business card.

We are a new startup based in Singapore called 'Brevora Technologies'.

We develop an array of financial solutions ranging from payment convenience to forex trading and remittance.

Our initial product is Pim - an application which allows user to pre-order food items which would be ready for pickup upon arrival.

We would like to see designs being in black and silver or whatever that looks appealing and exudes a fun and professional feel.

We're not picky as long as it doesn't look like common business cards will do.

I do have a current logo which i do not really like. It will be attached for reference sake

Info:

Brevora Technologies Pte. Ltd.
Company Registration no. 201678213K

FILE TO BE IN .AI and .PSD

Target Market(s)

-F&B (Online-Ordering)
-Finance(P2P Lending and Forex)

Industry/Entity Type

Finance

Contact Information for Business Card

Name
Position
Contact
Email
Address: 47 Merrow Street, Calder House, #14-03 Singapore 068215

Adrian Teo
Founder, Managing Director
+65 98471360
adrian.t@brevoratech.com

Kai Loh
Founder, Executive Director
+65 96603847
kai.l@brevoratech.com

Logo Text

Brevora Technologies

Font styles to use
Sans Serif

Requirements
Must have
• Something that has word play about link brev
• Minimalistic but also something that catches The Eye
• Gold/silver on white/black might be nice
• Animal logo ; horse, eagle, bull or bear
Nice to have
• Just make it look fun and cute
• Just a suggestion to make the Y of brevora stand out
Should not have
• Any landmarks of singapore
• Exclude Pte. Ltd.

```html
<!DOCTYPE html>
<html lang="en">
<head>
<meta charset="utf-8">
<title>Brevora Technologies – Business Card</title>
<link href="https://fonts.googleapis.com/css2?family=Open+Sans:wght@400;600;700&display=swap" rel="stylesheet">
<style>
  :root {
    --backdrop: #3a332e;
    --card-black: #050505;
    --card-panel: #111111;
    --gold: #f5a514;
    --silver: #9a9a9a;
    --silver-light: #e6e6e6;
    --text-light: #f2f2f2;
  }
  * { box-sizing: border-box; margin: 0; padding: 0; }
  html, body {
    width: 1200px; height: 844px; overflow: hidden;
    background: var(--backdrop);
    font-family: "Open Sans", Arial, sans-serif;
  }
  .stage {
    position: relative; width: 1200px; height: 844px;
    display: flex; align-items: center; justify-content: center; gap: 50px;
  }
  .card {
    position: relative; width: 525px; height: 300px; overflow: hidden;
    background: var(--card-black);
    box-shadow: 0 14px 30px rgba(0,0,0,.55);
  }

  /* Contact side */
  .card--contact .band {
    position: absolute; left: 0; right: 0; height: 12px; background: var(--gold);
  }
  .card--contact .band--top { top: 18px; }
  .card--contact .band--bottom { bottom: 0; }
  .card--contact .panel {
    position: absolute; left: 36px; right: 0; top: 30px; bottom: 26px;
    background: linear-gradient(100deg, var(--card-panel) 0%, #070707 60%, #1a1a1a 100%);
  }
  .contact {
    position: absolute; inset: 30px 0 12px 0;
    display: flex; flex-direction: column; align-items: center; justify-content: center;
    text-align: center; color: var(--text-light); font-size: 14px; line-height: 1.45;
  }
  .contact__name { color: var(--gold); font-weight: 700; font-size: 17px; line-height: 1.2; }
  .contact__role { margin-bottom: 20px; }
  .contact__address { margin-bottom: 16px; }
  .contact__line { display: flex; align-items: center; gap: 6px; }
  .contact__line svg { width: 12px; height: 12px; fill: var(--gold); }
  .contact__reg { margin-top: 22px; color: var(--gold); font-weight: 600; font-size: 14px; }
  .contact__reg strong { color: var(--text-light); font-weight: 700; }

  /* Brand side */
  .card--brand {
    background: radial-gradient(ellipse at 60% 40%, #2a2a2a 0%, #0c0c0c 55%, #030303 100%);
  }
  .tab { position: absolute; width: 22px; height: 44px; background: var(--gold); }
  .tab::after {
    content: ""; position: absolute; top: 0; width: 5px; height: 100%;
    background: linear-gradient(var(--silver-light), var(--silver));
  }
  .tab--left { left: 0; top: 150px; }
  .tab--left::after { right: -5px; }
  .tab--right { right: 0; top: 36px; }
  .tab--right::after { left: -5px; }
  .brand {
    position: absolute; left: 200px; top: 74px;
    display: flex; flex-direction: column; align-items: flex-start; gap: 14px;
  }
  .brand__square { width: 64px; height: 64px; background: var(--gold); margin-left: 16px; }
  .brand__name {
    color: var(--gold); font-weight: 400; font-size: 30px; letter-spacing: 1px;
    line-height: 1.1; text-transform: uppercase;
  }
  .brand__name span { display: block; font-size: 13px; letter-spacing: 2px; }
</style>
</head>
<body>
<main class="stage">
  <section class="card card--contact" aria-label="Business card contact side">
    <div class="band band--top"></div>
    <div class="panel"></div>
    <div class="contact">
      <p class="contact__name">Adrian Teo</p>
      <p class="contact__role">Founder, Managing Director</p>
      <p class="contact__address">47 Merrow Street, Calder House,<br>#14-03 Singapore 068215</p>
      <p class="contact__line">
        <svg viewBox="0 0 24 24" aria-hidden="true"><path d="M6.6 10.8a15.5 15.5 0 0 0 6.6 6.6l2.2-2.2c.3-.3.7-.4 1-.2 1.1.4 2.3.6 3.6.6.6 0 1 .4 1 1V20c0 .6-.4 1-1 1A17 17 0 0 1 3 4c0-.6.4-1 1-1h3.5c.6 0 1 .4 1 1 0 1.3.2 2.5.6 3.6.1.3 0 .7-.2 1z"/></svg>
        +65 98471360
      </p>
      <p class="contact__line">
        <svg viewBox="0 0 24 24" aria-hidden="true"><path d="M2 5h20v14H2z M2 5l10 8 10-8" stroke="#050505" stroke-width="1.5"/></svg>
        adrian.t@brevoratech.com
      </p>
      <p class="contact__reg">Company Registration no. <strong>201678213K</strong></p>
    </div>
    <div class="band band--bottom"></div>
  </section>

  <section class="card card--brand" aria-label="Business card brand side">
    <div class="tab tab--right"></div>
    <div class="tab tab--left"></div>
    <div class="brand">
      <div class="brand__square"></div>
      <p class="brand__name">Brevora<span>Technologies Pte. Ltd.</span></p>
    </div>
  </section>
</main>
</body>
</html>
```